Business card

creative business card for newly created national firm that specializes in high-density storage for retail markets. Looking for creativity and overall theme that will differentiate from others in this unique niche ...essentially a design that will provide instant recognition as we develop our identity in the marketplace. possible initial thoughts are attached with logo separately

Retail

```html
<!DOCTYPE html>
<html lang="en">
<head>
<meta charset="utf-8">
<title>Aisle Vault Systems – Business Card</title>
<link rel="stylesheet" href="https://fonts.googleapis.com/css2?family=Cabin:ital,wght@0,500;0,700;1,500&family=Tinos:ital@1&display=swap">
<style>
  :root {
    --card-bg: #ffffff;
    --brand-panel: #afdcf5;
    --brand-ink: #23526b;
    --brand-mark: #2f86b3;
    --name-ink: #111111;
    --tagline-ink: #2d5566;
  }
  html, body {
    margin: 0;
    padding: 0;
    width: 1200px;
    height: 720px;
    overflow: hidden;
    background: var(--card-bg);
  }
  .business-card {
    position: relative;
    width: 1200px;
    height: 720px;
    background: var(--card-bg);
    font-family: "Cabin", "Gill Sans", sans-serif;
  }
  .brand-panel {
    position: absolute;
    left: 164px;
    top: 235px;
    width: 403px;
    height: 476px;
    background: var(--brand-panel);
  }
  .brand-square {
    position: absolute;
    left: 295px;
    top: 110px;
    width: 140px;
    height: 140px;
    background: var(--brand-mark);
  }
  .brand-name {
    position: absolute;
    left: 190px;
    top: 440px;
    margin: 0;
    font-family: "Cabin", "Gill Sans", sans-serif;
    font-weight: 500;
    font-size: 54px;
    line-height: 62px;
    letter-spacing: 2px;
    color: var(--brand-ink);
    text-transform: uppercase;
  }
  .contact {
    position: absolute;
    left: 640px;
    width: 465px;
    text-align: center;
  }
  .contact-name {
    top: 182px;
    margin: 0;
    font-weight: 700;
    font-size: 42px;
    letter-spacing: 1.5px;
    color: var(--name-ink);
  }
  .contact-phone {
    top: 236px;
    margin: 0;
    font-weight: 500;
    font-size: 31px;
    color: var(--name-ink);
  }
  .tagline {
    top: 388px;
    margin: 0;
    font-family: "Tinos", "Times New Roman", serif;
    font-style: italic;
    font-size: 38px;
    color: var(--tagline-ink);
  }
  .website {
    top: 532px;
    margin: 0;
    font-style: italic;
    font-weight: 500;
    font-size: 25px;
    color: var(--name-ink);
  }
</style>
</head>
<body>
  <main class="business-card">
    <div class="brand-panel"></div>
    <div class="brand-square"></div>
    <p class="brand-name">Aisle<br>Vault<br>Systems</p>

    <h1 class="contact contact-name">DANA WHITCOMB</h1>
    <p class="contact contact-phone">855-STACK-NOW</p>
    <p class="contact tagline">Innovate your space</p>
    <p class="contact website">www.aislevaultsystems.com</p>
  </main>
</body>
</html>
```